Verodex business card

Business card for sustainable investment company called "Verodex". Verodex is an exchange platform selling carbon credits between buyers and sellers. Carbon Credits are an environmental commodity for reducing global carbon emissions.

the card should obviously have our logo and the theme should be sustainability/environment mixed with a trading platform.

Contact Information for Business Card

Logo, Name, Title, Phone, Email

Colors
0054AA
0677BA
7BADD7
CADEEF
E8F1F8
0094D4
00A9DD
6FCCEA
C7EBF8
E9F6FB
00AB8E
00BBA5
67D7C9
C6EFE9
E9F9F6
59FF00
82FF00
B8FF75
E3FFCB
F4FFEA

```html
<!DOCTYPE html>
<html lang="en">
<head>
<meta charset="utf-8">
<title>Verodex Business Card</title>
<link href="https://fonts.googleapis.com/css2?family=Montserrat:wght@400;500;700;800&display=swap" rel="stylesheet">
<style>
  :root{
    --navy:#172a50;
    --ink:#1b2d55;
    --sky:#4fa3d4;
    --name-blue:#3d82cc;
    --paper:#ffffff;
    --table:#e6e9ee;
    --text:#1d1d1f;
  }
  *{box-sizing:border-box;margin:0;padding:0}
  html,body{width:1200px;height:900px;overflow:hidden}
  body{background:var(--table);font-family:"Montserrat",sans-serif;position:relative}
  .card{position:absolute;left:268px;width:665px;height:380px;border-radius:18px;overflow:hidden;box-shadow:0 10px 30px rgba(20,30,60,.18)}
  .card-front{top:40px;background:var(--paper)}
  .card-back{top:470px;background:var(--navy);display:flex;align-items:center;justify-content:center}
  .wave{position:absolute;left:0;top:0;width:665px;height:380px}
  .brand{position:absolute;left:48px;top:82px;display:flex;align-items:center;gap:14px}
  .brand-mark{width:26px;height:26px;background:var(--sky);border-radius:50%}
  .brand-name{font-weight:800;font-size:40px;letter-spacing:1px;color:var(--ink);text-transform:uppercase}
  .person{position:absolute;right:62px;top:170px;text-align:right;text-transform:uppercase}
  .person-name{font-weight:800;font-size:24px;line-height:28px;color:var(--name-blue);letter-spacing:1px}
  .person-title{font-weight:500;font-size:15px;line-height:18px;color:var(--text);letter-spacing:1.5px;margin-top:2px}
  .divider{position:absolute;left:40px;right:62px;top:236px;height:1.5px;background:var(--sky)}
  .accent-tab{position:absolute;right:0;top:214px;width:16px;height:40px;background:var(--sky)}
  .contacts{position:absolute;left:36px;top:262px;list-style:none;font-size:14px;color:var(--text);line-height:24px}
  .contacts li{display:flex;align-items:center;gap:9px}
  .contacts svg{width:13px;height:13px;fill:var(--sky)}
  .address{position:absolute;right:62px;top:262px;font-size:14px;color:var(--text);line-height:24px;text-align:right}
  .back-brand{display:flex;align-items:center;gap:22px}
  .back-brand .brand-mark{width:40px;height:40px}
  .back-brand .brand-name{font-size:64px;color:var(--paper)}
</style>
</head>
<body>
  <section class="card card-front">
    <svg class="wave" viewBox="0 0 665 380" aria-hidden="true">
      <path d="M170 14 C300 10 380 40 450 72 C520 104 580 116 665 112 L665 104 C585 106 525 94 458 62 C390 30 310 4 200 0 Z" fill="#4fa3d4"/>
      <path d="M215 0 C320 4 400 30 465 58 C530 86 590 98 665 96 L665 0 Z" fill="#172a50"/>
    </svg>
    <div class="brand">
      <span class="brand-mark"></span>
      <span class="brand-name">Verodex</span>
    </div>
    <div class="person">
      <p class="person-name">Dana Holloway</p>
      <p class="person-title">Manager</p>
    </div>
    <div class="divider"></div>
    <div class="accent-tab"></div>
    <ul class="contacts">
      <li><svg viewBox="0 0 24 24"><path d="M6.6 10.8a15 15 0 0 0 6.6 6.6l2.2-2.2a1 1 0 0 1 1-.25 11.4 11.4 0 0 0 3.6.57 1 1 0 0 1 1 1V20a1 1 0 0 1-1 1A17 17 0 0 1 3 4a1 1 0 0 1 1-1h3.5a1 1 0 0 1 1 1c0 1.25.2 2.45.57 3.57a1 1 0 0 1-.25 1z"/></svg>555-014-2290</li>
      <li><svg viewBox="0 0 24 24"><path d="M2 5h20v14H2z"/></svg>hello@verodex-mail.com</li>
      <li><svg viewBox="0 0 24 24"><circle cx="12" cy="12" r="10"/></svg>www.verodex-site.com</li>
    </ul>
    <p class="address">2217 Alder Creek Rd. Harbor Point<br>Ave Lakeview, MN 05514</p>
  </section>

  <section class="card card-back">
    <div class="back-brand">
      <span class="brand-mark"></span>
      <span class="brand-name">Verodex</span>
    </div>
  </section>
</body>
</html>
```